BOLD & MINIMALIST DESIGN NEEDED

We want a very bold but minimalistic business card design that is impactful and utilizes both sides of the business card. Our current logo is included for your use.

We want bold fonts and good use of negative space. We don't want the logo to overpower the design.

Target Market(s)

Professionals who are building new commercial buildings.

Industry/Entity Type

Construction

Contact Information for Business Card

Name, Title, email, office phone, cell phone, website

Font styles to use
Serif
Sans Serif

Requirements
Must have
• Bold design!

```html
<!DOCTYPE html>
<html lang="en">
<head>
<meta charset="utf-8">
<title>Ridgecrest Design + Build — Business Card</title>
<link rel="stylesheet" href="https://fonts.googleapis.com/css2?family=Montserrat:wght@400;500;700;800&display=swap">
<style>
  :root{
    --bg:#3a3a3a;
    --card:#1c1c1c;
    --card-edge:#8cc63f;
    --accent:#8cc63f;
    --text:#f2f2f2;
    --muted:#d6d6d6;
    --ghost:#2b2b2b;
  }
  *{margin:0;padding:0;box-sizing:border-box;}
  html,body{width:1200px;height:791px;overflow:hidden;}
  body{
    background:var(--bg);
    font-family:"Montserrat",Arial,sans-serif;
    position:relative;
  }
  .card{
    position:absolute;
    width:560px;height:320px;
    background:var(--card);
    border-bottom:3px solid var(--card-edge);
    border-left:2px solid var(--card-edge);
    box-shadow:0 18px 40px rgba(0,0,0,.45);
  }
  .card--front{left:40px;top:70px;}
  .card--back{left:600px;top:400px;}

  /* front */
  .brand{
    position:absolute;left:40px;top:0;bottom:0;width:230px;
    display:flex;flex-direction:column;justify-content:center;align-items:flex-start;
  }
  .brand__mark{display:flex;align-items:center;gap:10px;}
  .brand__dot{width:16px;height:16px;border-radius:50%;background:var(--accent);}
  .brand__name{
    font-weight:800;font-size:30px;letter-spacing:1px;color:var(--text);line-height:1;
  }
  .brand__tag{
    margin-top:8px;margin-left:26px;
    font-weight:800;font-size:11px;letter-spacing:5px;color:var(--text);
  }
  .divider{
    position:absolute;left:285px;top:95px;width:2px;height:130px;background:var(--accent);
  }
  .contact{position:absolute;left:315px;top:78px;}
  .contact__name{font-weight:700;font-size:20px;color:var(--accent);letter-spacing:.5px;}
  .contact__title{font-weight:400;font-size:13px;color:var(--muted);margin-top:3px;}
  .contact__list{list-style:none;margin-top:28px;}
  .contact__item{
    display:flex;align-items:center;gap:9px;
    font-size:12.5px;color:var(--muted);margin-bottom:7px;
  }
  .contact__icon{width:12px;height:12px;flex:none;}

  /* back */
  .back-mark{
    position:absolute;inset:0;display:flex;align-items:center;justify-content:center;
  }
  .back-mark__name{
    font-weight:800;font-size:40px;letter-spacing:2px;color:var(--ghost);
  }
</style>
</head>
<body>

<section class="card card--front" aria-label="Business card front">
  <div class="brand">
    <div class="brand__mark">
      <span class="brand__dot"></span>
      <span class="brand__name">RIDGECREST</span>
    </div>
    <div class="brand__tag">DESIGN + BUILD</div>
  </div>

  <div class="divider"></div>

  <div class="contact">
    <h1 class="contact__name">MARTIN COLES</h1>
    <p class="contact__title">President</p>
    <ul class="contact__list">
      <li class="contact__item">
        <svg class="contact__icon" viewBox="0 0 24 24" fill="var(--accent)"><path d="M6.6 10.8a15.1 15.1 0 0 0 6.6 6.6l2.2-2.2c.3-.3.7-.4 1-.2 1.1.4 2.3.6 3.6.6.6 0 1 .4 1 1V20c0 .6-.4 1-1 1A17 17 0 0 1 3 4c0-.6.4-1 1-1h3.5c.6 0 1 .4 1 1 0 1.3.2 2.5.6 3.6.1.3 0 .7-.2 1z"/></svg>
        555-014-2200
      </li>
      <li class="contact__item">
        <svg class="contact__icon" viewBox="0 0 24 24" fill="none" stroke="var(--muted)" stroke-width="2"><rect x="6" y="2" width="12" height="20" rx="2"/><line x1="11" y1="18" x2="13" y2="18"/></svg>
        555-014-2201
      </li>
      <li class="contact__item">
        <svg class="contact__icon" viewBox="0 0 24 24" fill="var(--accent)"><path d="M2 5h20v14H2z"/><path d="M2 5l10 8 10-8" fill="none" stroke="var(--card)" stroke-width="2"/></svg>
        m.coles@rdb-build.com
      </li>
      <li class="contact__item">
        <svg class="contact__icon" viewBox="0 0 24 24" fill="none" stroke="var(--accent)" stroke-width="2"><circle cx="12" cy="12" r="10"/><path d="M2 12h20M12 2c3 3 3 17 0 20M12 2c-3 3-3 17 0 20"/></svg>
        www.rdb-build.com
      </li>
    </ul>
  </div>
</section>

<section class="card card--back" aria-label="Business card back">
  <div class="back-mark">
    <span class="back-mark__name">RIDGECREST</span>
  </div>
</section>

</body>
</html>
```